Martial Arts Website

Redevelopment of existing martial arts website.

The academy teaches traditional shaolin martial arts, including Shaolin Kung Fu, Wu Shu, Tai Chi, Qigong and Wing Chun and the site needs to reflect the traditional roots (eg, no tacky boxing imagery)

Existing website is www.copperlantern.com.au to get a feel for the desired color scheme (black, green and red). The exact colors can be tweaked though. Please only reuse the logo and font (Karate) - there isnt anything else from the current design that needs to remain.

The current website includes links to a ClipHarbor channel that includes demonstrations of the training conducted to better guide the design.

The new website site map will be:
1. Home
2. Programs - summary page describing each form of training
a. Tiny Otters
b. Kids Kung Fu
c. Youth Kung Fu
d. Adults Kung Fu
e. Wing Chun
f. Tai Chi & Qigong
g. Weaponry Classes
h. 72 Arts of Shaolin Conditioning Program
i. Acrobatics and Wu Shu
j. Fitness Boxing
3. Timetable
4. Coaches - summary page describing all coaches
a. Sifu (Master)
b. Sihing Kit
c. Sihing Sam
d. Sihing Marcus
X. ... up to 10 or so coaches
5. Member Zone
6. Contact Us
Updates

Logo now attached to brief - sorry I only have it in PDF

Just to clarify, I am only expecting a PSD design - no HTML required

Reason: Thanks for the designs, we love a lot of them just require a little extra time to tweak the designs and establish the potential. Thanks for your understanding and efforts.

Target Market(s)

Parents, teenagers, young adults, adults, elderly

Industry/Entity Type

Training

Requirements
Must have
• Chinese kung fu dragon imagery throughout the background
Links to Chatterly and ClipHarbor channel
Promo/icon in the header "Try 2 free classes now"
Home page should include an embedded ClipHarbor video

```html
<!DOCTYPE html>
<html lang="en">
<head>
<meta charset="utf-8">
<title>Copper Lantern Martial Arts Academy</title>
<link href="https://fonts.googleapis.com/css2?family=Arimo:ital,wght@0,400;0,700;1,400;1,700&family=Libre+Baskerville:wght@400;700&family=Bangers&display=swap" rel="stylesheet">
<style>
:root{
  --black:#000;
  --ink:#1a1a1a;
  --green:#2f8a25;
  --green-dark:#24661d;
  --red:#b50d0d;
  --red-band:#c9180b;
  --grey:#7a7a7a;
  --grey-light:#a8a8a8;
  --white:#fff;
  --text:#222;
}
*{box-sizing:border-box;margin:0;padding:0}
html,body{width:1176px;height:1200px;overflow:hidden;background:var(--black);font-family:Arimo,Arial,sans-serif;color:var(--text)}
.page{position:relative;width:1176px;height:1200px}
.abs{position:absolute}

/* header */
.header{left:0;top:0;width:1176px;height:218px;background:var(--black)}
.brand{left:0;top:60px;width:1176px;text-align:center}
.brand-name{display:inline-flex;align-items:center;gap:18px;font-family:"Libre Baskerville",Georgia,serif;font-weight:700;font-size:52px;color:var(--green)}
.brand-dot{width:30px;height:30px;border-radius:50%;background:var(--green)}
.brand-sub{margin-top:22px;font-family:"Libre Baskerville",Georgia,serif;font-weight:700;font-size:17px;letter-spacing:3px;color:var(--red)}
.brand-tag{margin-top:6px;font-size:10px;letter-spacing:2.5px;color:var(--white)}

/* nav */
.nav{left:0;top:218px;width:1176px;height:40px;background:var(--white)}
.nav ul{list-style:none;display:flex;position:absolute;left:292px;top:0;height:40px;align-items:center}
.nav li{font-size:12.5px;color:#555;padding:0 15px;border-left:1px solid #ccc;line-height:22px}
.nav li.active{background:var(--red);color:var(--white);border:none;height:44px;margin-top:-8px;padding:25px 12px 0;line-height:14px;margin-right:13px}

/* hero */
.hero{left:0;top:258px;width:1176px;height:411px;background:#1e1e1e}
.welcome{left:16px;top:0;width:386px;height:411px;background:linear-gradient(180deg,#6a6a6a,#8e8e8e 60%,#7b7b7b);text-align:center;color:var(--white);font-family:"Libre Baskerville",Georgia,serif}
.welcome h1{font-size:22px;margin-top:28px;letter-spacing:.5px}
.rule{border-top:1px dotted #ddd;margin:0 52px}
.welcome h1+.rule{margin-top:10px}
.welcome p{font-size:29px;line-height:33px;padding:10px 30px 12px;font-weight:400}
.btn-red{display:inline-block;margin-top:20px;background:var(--red);border:1px solid #e04;color:var(--white);font-family:Arimo,sans-serif;font-size:12px;padding:5px 16px;width:228px}
.photo{left:403px;top:0;width:544px;height:411px;background:linear-gradient(160deg,#cfcac2,#a89474 55%,#8c6e48)}
.free{left:746px;top:10px;background:var(--green);color:var(--white);font-weight:700;font-size:13.5px;padding:8px 12px;border-bottom:3px solid var(--green-dark)}
.slide-arrow{top:204px;width:0;height:0;border-top:8px solid transparent;border-bottom:8px solid transparent}
.caption{left:515px;top:252px;width:432px;height:130px;background:rgba(235,230,222,.82);padding:10px 12px}
.caption h2{font-family:Bangers,cursive;font-weight:400;font-size:26px;color:var(--red);letter-spacing:1px}
.caption p{font-size:13px;line-height:19px;color:#333}
.classes{left:947px;top:0;width:215px;height:411px;background:linear-gradient(180deg,#a8a8a8,#888 55%,#6a6a6a)}
.classes h3{font-family:"Libre Baskerville",Georgia,serif;font-size:17px;color:var(--white);margin:12px 24px 0;padding-bottom:6px;border-bottom:1px dotted #ddd;width:148px}
.classes ul{list-style:none;margin-top:6px}
.classes li{position:relative;padding-left:52px;height:37.5px;color:var(--white);font-style:italic;font-weight:700;font-size:12.5px;line-height:13px;padding-top:3px}
.classes li small{display:block;font-weight:400;font-size:9.5px}
.classes li::before{content:"";position:absolute;left:18px;top:3px;width:16px;height:16px;border-radius:50%;background:var(--red)}
.classes li::after{content:"";position:absolute;left:24px;top:7px;border-left:6px solid #fff;border-top:4px solid transparent;border-bottom:4px solid transparent}

/* programs band */
.band{left:0;top:669px;width:1176px;height:260px;background:linear-gradient(180deg,var(--red-band),#b00e08)}
.card{top:20px;width:374px;height:215px;background:var(--green)}
.video{left:0;top:0;width:241px;height:215px;background:var(--black)}
.video .shot{position:absolute;left:0;top:30px;width:241px;height:135px}
.controls{position:absolute;left:0;bottom:0;width:241px;height:44px;background:#2a2a2a;color:#eee;font-size:10px;font-weight:700}
.controls .track{position:absolute;left:6px;top:6px;width:229px;height:3px;background:#555}
.controls .knob{position:absolute;left:2px;top:1px;width:12px;height:12px;border-radius:50%;background:#ddd}
.controls .play{position:absolute;left:20px;top:20px;border-left:11px solid #aaa;border-top:7px solid transparent;border-bottom:7px solid transparent}
.controls .time{position:absolute;left:92px;top:21px}
.prog{left:241px;top:0;width:133px;height:215px;background:linear-gradient(180deg,#3b9a2c,#2c7a22);color:var(--white);padding:16px 0 0 10px}
.prog h4{font-family:Bangers,cursive;font-weight:400;font-size:30px;line-height:30px;letter-spacing:1px}
.prog .kind{font-family:"Libre Baskerville",Georgia,serif;font-size:13px;letter-spacing:4px;border-top:1px dotted #cfe;padding-top:3px;margin-top:2px;width:118px}
.prog p{font-style:italic;font-size:12.5px;line-height:16px;margin-top:14px}
.learn{position:absolute;left:14px;top:164px;background:var(--red);font-size:11.5px;font-weight:700;padding:5px 8px;color:var(--white)}

/* footer */
.footer{left:0;top:929px;width:1176px;height:179px;background:var(--white)}
.col{top:16px;height:150px}
.col+.col{border-left:1px dotted #888}
.col h5{font-family:"Libre Baskerville",Georgia,serif;font-size:15px;font-weight:700;color:#222;text-align:center}
.item{position:absolute;font-size:11.5px;line-height:13.5px;color:#222}
.item b{display:block}
.icon{position:absolute}
.badge{position:absolute;background:#888}
.bottom{left:0;top:1108px;width:1176px;height:92px;background:var(--ink)}
.bottom p{position:absolute;left:4px;top:31px;width:1146px;border-top:1px dotted #555;padding-top:12px;font-size:11.5px;color:#999}
</style>
</head>
<body>
<div class="page">

  <header class="header abs">
    <div class="brand abs">
      <div class="brand-name"><span class="brand-dot"></span>Copper Lantern</div>
      <div class="brand-sub">MARTIAL ARTS ACADEMY</div>
      <div class="brand-tag">TRADITIONAL KUNG FU &amp; TAI CHI TRAINING CENTRE</div>
    </div>
  </header>

  <nav class="nav abs">
    <ul>
      <li class="active">HOME</li>
      <li>PROGRAMS</li>
      <li>TIMETABLE</li>
      <li>COACHES</li>
      <li>MEMBER ZONE</li>
      <li>CONTACT US</li>
    </ul>
  </nav>

  <section class="hero abs">
    <div class="welcome abs">
      <h1>WELCOME</h1>
      <div class="rule"></div>
      <p>to the Home of Traditional Shaolin Kung Fu, Wing Chun Kung Fu, Tai Chi &amp; Qigong for all ages and physical capabilities.</p>
      <div class="rule"></div>
      <span class="btn-red">VIEW CLASS TIMES &amp; DAYS ▮</span>
    </div>

    <div class="photo abs" role="img" aria-label="Students in white uniforms practising a low kung fu stance on a wooden floor"></div>
    <div class="free abs">TRY 2 FREE CLASSES NOW! ▶</div>
    <span class="slide-arrow abs" style="left:416px;border-right:10px solid #fff"></span>
    <span class="slide-arrow abs" style="left:921px;border-left:10px solid #fff"></span>
    <div class="caption abs">
      <h2>Kids Kung Fu</h2>
      <p>Kids Kung Fu – ages 6 to 11. Practical, Responsible Instruction. Plus, we specialize in powerful character development skills in a positive environment. Kids learn self defence NOT fighting, anti bullying techniques.</p>
    </div>

    <aside class="classes abs">
      <h3>ALL CLASSES</h3>
      <ul>
        <li>Tiny Otters<small>Ages 4 - 6</small></li>
        <li>Kids Kung Fu<small>Ages 6 - 11</small></li>
        <li>Youth Kung Fu<small>Ages 11 - 15</small></li>
        <li>Adults Kung Fu<small>Ages 15 &amp; over</small></li>
        <li>Wing Chun<small>Ages 13 &amp; over</small></li>
        <li>Tai Chi &amp; Qigong<small>All ages</small></li>
        <li>Weaponry Classes<small>Ages 5 and over</small></li>
        <li>72 Arts of Shaolin<small>Conditioning Program</small></li>
        <li>Acrobatics and Wu Shu<small>Performance Team</small></li>
        <li>Fitness Boxing</li>
      </ul>
    </aside>
  </section>

  <section class="band abs">
    <article class="card abs" style="left:16px">
      <div class="video abs">
        <div class="shot" role="img" aria-label="Video still of a martial artist training on a hilltop" style="background:linear-gradient(180deg,#b9b2ab,#7d7068 60%,#4a3d36)"></div>
        <div class="controls"><span class="track"></span><span class="knob"></span><span class="play"></span><span class="time">0:00 / 0:00</span></div>
      </div>
      <div class="prog abs">
        <h4>Adult</h4><div class="kind">PROGRAMS</div>
        <p>Classes include<br>Adult Kung Fu,<br>Wing Chun,<br>Weaponry &amp; more</p>
        <span class="learn">LEARN MORE</span>
      </div>
    </article>
    <article class="card abs" style="left:401px">
      <div class="video abs">
        <div class="shot" role="img" aria-label="Video still of children sparring in a class" style="background:linear-gradient(180deg,#6a6a6a,#3c3c3c 60%,#2a2a2a)"></div>
        <div class="controls"><span class="track"></span><span class="knob"></span><span class="play"></span><span class="time">0:00 / 0:00</span></div>
      </div>
      <div class="prog abs">
        <h4>Children</h4><div class="kind">PROGRAMS</div>
        <p>Classes include:<br>Tiny Otters,<br>Kids Kung Fu,<br>&amp; Youth Kung Fu</p>
        <span class="learn">LEARN MORE</span>
      </div>
    </article>
    <article class="card abs" style="left:786px">
      <div class="video abs">
        <div class="shot" role="img" aria-label="Video still of a fitness workout on a mat" style="background:linear-gradient(180deg,#6f6a5c,#8a8580 60%,#706a80)"></div>
        <div class="controls"><span class="track"></span><span class="knob"></span><span class="play"></span><span class="time">0:00 / 0:00</span></div>
      </div>
      <div class="prog abs">
        <h4>Fitness</h4><div class="kind">PROGRAMS</div>
        <p>Get fit with Fitness<br>Boxing classes,<br>Tai Chi &amp; Qigong<br>and more</p>
        <span class="learn">LEARN MORE</span>
      </div>
    </article>
  </section>

  <footer class="footer abs">
    <div class="col abs" style="left:0;width:272px">
      <h5 style="text-align:left;padding-left:69px">Contact</h5>
      <svg class="icon" style="left:38px;top:44px" width="14" height="28" viewBox="0 0 14 28"><rect x="1" y="1" width="12" height="26" rx="2" fill="#555"/><rect x="3" y="5" width="8" height="15" fill="#ddd"/></svg>
      <div class="item" style="left:69px;top:46px"><b>Phone:</b>(02) 4700 1836</div>
      <svg class="icon" style="left:30px;top:92px" width="26" height="16" viewBox="0 0 26 16"><rect x="1" y="1" width="24" height="14" fill="none" stroke="#555" stroke-width="2"/><path d="M1 1 13 10 25 1" fill="none" stroke="#555" stroke-width="2"/></svg>
      <div class="item" style="left:69px;top:88px"><b>Email:</b>kwoon@copperlantern.com.au</div>
    </div>
    <div class="col abs" style="left:272px;width:317px">
      <h5>News &amp; Downloads</h5>
      <svg class="icon" style="left:62px;top:46px" width="20" height="22" viewBox="0 0 20 22"><rect x="1" y="1" width="14" height="17" fill="#999"/><rect x="5" y="4" width="14" height="17" fill="#666"/></svg>
      <div class="item" style="left:96px;top:46px"><b>Newsletter</b>Click here to download</div>
      <svg class="icon" style="left:62px;top:88px" width="20" height="20" viewBox="0 0 20 20"><circle cx="10" cy="10" r="8" fill="none" stroke="#666" stroke-width="2.5"/><circle cx="10" cy="10" r="3" fill="none" stroke="#666" stroke-width="2"/></svg>
      <div class="item" style="left:96px;top:88px"><b>News &amp; Updates</b>Click here to view</div>
    </div>
    <div class="col abs" style="left:589px;width:293px">
      <h5>Social Media</h5>
      <span class="badge" style="left:48px;top:44px;width:28px;height:28px;border-radius:4px;background:#b22"></span>
      <div class="item" style="left:94px;top:46px"><b>ClipHarbor</b>View our channel here</div>
      <span class="badge" style="left:48px;top:86px;width:28px;height:28px;border-radius:4px;background:#3b5998"></span>
      <div class="item" style="left:94px;top:88px;width:140px"><b>Chatterly</b>222 people like this. Be the first of your friends.</div>
      <div class="item" style="left:52px;top:128px;border:1px solid #bbb;padding:3px 5px;background:#eef;color:#3b5998">Like</div>
    </div>
    <div class="col abs" style="left:882px;width:294px">
      <h5>Alliances &amp; Accreditation</h5>
      <span class="badge" style="left:81px;top:46px;width:66px;height:48px"></span>
      <span class="badge" style="left:164px;top:44px;width:52px;height:52px;border-radius:50%;background:#b00"></span>
      <span class="badge" style="left:78px;top:104px;width:70px;height:44px;border-radius:50%;background:#222"></span>
      <span class="badge" style="left:164px;top:100px;width:56px;height:52px;background:#1f5fb0"></span>
    </div>
  </footer>

  <div class="bottom abs">
    <p>Copyright © 2012 - Copper Lantern Martial Arts Pty Ltd. Kung Fu and Tai Chi Training Centre - Unit 7, 22 Harlow Street, Westbrook NSW 2790</p>
  </div>

</div>
</body>
</html>
```